Banner to be displayed at local Farmers Market Booth.

Graphic Design Brief: Farmers Market Banner Contest

Project Overview:We are seeking talented graphic designers to create a visually appealing banner for our booth at the local farmers market. Our company specializes in healthy, all-natural dog and cat treats, and we want a banner that captures our brand identity while drawing in pet owners who value quality and nutrition for their furry friends.

Banner Specifications:

Size: 24 inches x 60 inches (Horizontal orientation) 24" High X 60 wide

Theme: Vintage/Retro

Style: Warm, inviting, nostalgic with a touch of rustic charm

Colors: Earthy, muted tones such as warm browns, soft greens, and creamy yellows. Pops of red or blue may be used sparingly for accents. OR Black and White with gray scales. Would like to see both

Typography: Retro-style fonts that are readable and align with the vintage aesthetic.

Key Elements to Include: website (www.moltbyfarms.com)

Company Name: Moltby Farms

Tagline: " Simply Honest Bites "
Imagery: Illustrations or stylized graphics of happy dogs and cats, possibly interacting with treats.

Emphasis on Natural Ingredients: Icons or design elements that subtly suggest freshness and quality (e.g., leaves, wheat, bones, or paw prints).

Farmers Market Appeal: A design that blends well with the artisanal, handmade, and farm-fresh atmosphere of the market.

Design Considerations:

The banner should be easily readable from a distance.

A balanced composition that doesn't feel overcrowded.

Should evoke trust and warmth while maintaining a professional look.

Avoid overly modern or sleek elements that don’t align with the vintage aesthetic.

Submission Requirements:

High-resolution digital file in PDF or AI format.

CMYK color mode for printing purposes.

Must include a mockup or preview of how it would look in a real farmers market setting.

We look forward to seeing your creative interpretations of our brand! If you have any questions, feel free to reach out.

Font styles to use
Other font styles liked:
• See attachement

Requirements
Nice to have
• Retro/Vintage,playful BUT NOT whimsical

```html
<!DOCTYPE html>
<html lang="en">
<head>
<meta charset="utf-8">
<title>Moltby Farms — Market Banner</title>
<link rel="stylesheet" href="https://fonts.googleapis.com/css2?family=Rubik+Mono+One&family=Libre+Caslon+Text:wght@400;700&display=swap">
<style>
  :root {
    --page: #e9e6e1;
    --ink: #161616;
    --ink-soft: #2a2a2a;
    --cream: #f1efea;
    --orange: #e8843a;
    --orange-deep: #c8561f;
    --art-light: #cfcac2;
    --art-dark: #6e6a64;
  }
  html, body {
    margin: 0;
    width: 1200px;
    height: 944px;
    overflow: hidden;
    background: var(--page);
  }
  .banner {
    position: absolute;
    left: 20px;
    top: 241px;
    width: 1510px;
    height: 600px;
    transform: scale(0.7682);
    transform-origin: 0 0;
    overflow: hidden;
    background: var(--ink);
    box-shadow: 0 8px 0 var(--orange-deep);
  }
  .banner-ground {
    position: absolute;
    inset: 0;
    width: 1510px;
    height: 600px;
  }
  .brand-name {
    position: absolute;
    left: 18px;
    top: 34px;
    width: 905px;
    margin: 0;
    text-align: center;
    font-family: "Rubik Mono One", sans-serif;
    font-weight: 400;
    color: var(--cream);
    line-height: 1;
  }
  .brand-name .line {
    display: block;
    font-size: 118px;
    letter-spacing: 4px;
  }
  .brand-name .line + .line {
    margin-top: 18px;
  }
  .website {
    position: absolute;
    left: 18px;
    top: 312px;
    width: 905px;
    text-align: center;
    font-family: "Libre Caslon Text", serif;
    font-size: 38px;
    letter-spacing: 7px;
    color: var(--cream);
    text-transform: uppercase;
  }
  .tagline {
    position: absolute;
    left: 48px;
    top: 432px;
    margin: 0;
    font-family: "Libre Caslon Text", serif;
    font-weight: 700;
    font-size: 68px;
    letter-spacing: 4px;
    text-transform: uppercase;
    color: var(--cream);
    text-shadow: -3px 3px 0 var(--ink), -5px 5px 0 var(--ink);
    white-space: nowrap;
  }
  .descriptor {
    position: absolute;
    left: 48px;
    top: 520px;
    margin: 0;
    font-family: "Libre Caslon Text", serif;
    font-size: 53px;
    letter-spacing: 1px;
    text-transform: uppercase;
    color: var(--cream);
    white-space: nowrap;
  }
  .pet-art {
    position: absolute;
    left: 935px;
    top: 60px;
    width: 430px;
    height: 370px;
    border-radius: 14px;
    background: radial-gradient(ellipse at 55% 40%, var(--art-light) 0%, #a9a49c 55%, var(--art-dark) 100%);
  }
  .corner-mark {
    position: absolute;
    left: 1375px;
    top: 70px;
    width: 125px;
    display: flex;
    align-items: center;
    gap: 6px;
    font-family: "Libre Caslon Text", serif;
    font-size: 17px;
    color: var(--cream);
    line-height: 1.1;
  }
  .corner-mark .dot {
    flex: none;
    width: 14px;
    height: 14px;
    border-radius: 50%;
    background: var(--cream);
  }
</style>
</head>
<body>
  <main class="banner">
    <svg class="banner-ground" viewBox="0 0 1510 600" aria-hidden="true">
      <rect width="1510" height="600" fill="var(--ink)"/>
      <polygon fill="var(--orange)"
        points="0,388 40,392 70,380 110,398 150,384 190,396 230,378 260,392 300,384 340,400 380,382 420,394 470,380 510,398 560,386 600,396 640,378 690,394 730,384 770,398 820,382 860,392 900,384 940,400 980,396 1510,410 1510,600 0,600"/>
      <polyline fill="none" stroke="var(--cream)" stroke-width="2" opacity="0.5"
        points="0,388 40,392 70,380 110,398 150,384 190,396 230,378 260,392 300,384 340,400 380,382 420,394 470,380 510,398 560,386 600,396 640,378 690,394 730,384 770,398 820,382 860,392 900,384 940,400"/>
    </svg>

    <h1 class="brand-name">
      <span class="line">MOLTBY</span>
      <span class="line">FARMS</span>
    </h1>

    <div class="website">www.moltbyfarms.com</div>

    <div class="pet-art" role="img" aria-label="Engraved-style illustration of a tabby cat beside a smiling golden retriever resting its paws by a bowl of yellow treats"></div>

    <div class="corner-mark"><span class="dot"></span><span>Moltby Farms</span></div>

    <p class="tagline">Simply Honest Bites</p>
    <p class="descriptor">Purveyors of Premium Pet Food &amp; Treats</p>
  </main>
</body>
</html>
```